Mindfulness School for Children -- Business Cards

We're looking for business cards for our school directors and owners. We're a mindfulness school for children called little lanterns. Attached are our logos/icons.

```html
<!DOCTYPE html>
<html lang="en">
<head>
<meta charset="utf-8">
<title>little lanterns — Business Cards</title>
<link href="https://fonts.googleapis.com/css2?family=Alegreya:wght@400&family=Source+Sans+3:wght@400;600&display=swap" rel="stylesheet">
<style>
  :root {
    --backdrop: #2b2e36;
    --card-white: #eceef2;
    --teal: #4c9db3;
    --teal-deep: #2f87a0;
    --sage: #6aaa8f;
    --ink: #1f2328;
    --emboss: #9fcad6;
  }
  * { box-sizing: border-box; margin: 0; padding: 0; }
  html, body { width: 1200px; height: 1000px; overflow: hidden; }
  body {
    background: var(--backdrop);
    font-family: "Source Sans 3", sans-serif;
    position: relative;
  }
  .card {
    position: absolute;
    top: 352px;
    width: 520px;
    height: 297px;
    overflow: hidden;
  }
  .card-front { left: 70px; background: var(--card-white); }
  .card-back { left: 610px; background: var(--teal); }

  .accent-bar {
    position: absolute; left: 0; top: 178px;
    width: 7px; height: 26px; background: var(--teal);
  }
  .deco-circle { position: absolute; border-radius: 50%; }
  .card-front .deco-circle {
    width: 300px; height: 300px; right: -150px; top: -2px;
    background: var(--teal);
  }
  .card-back .deco-circle {
    width: 300px; height: 300px; left: -150px; top: -2px;
    background: var(--card-white);
  }

  .wordmark {
    font-family: "Alegreya", serif;
    font-weight: 400;
    position: absolute;
    white-space: nowrap;
  }
  .card-front .wordmark {
    left: 60px; top: 56px; font-size: 40px; color: var(--sage);
  }
  .card-back .wordmark {
    left: 190px; top: 110px; font-size: 44px; color: var(--emboss);
  }
  .wordmark-dot {
    display: inline-block; width: 10px; height: 10px; border-radius: 50%;
    background: currentColor; margin-right: 10px; vertical-align: middle;
  }

  .person { position: absolute; left: 62px; top: 128px; }
  .person-name { font-size: 18px; font-weight: 600; color: var(--sage); }
  .person-name .surname { color: var(--teal-deep); }
  .person-role { font-size: 13px; color: var(--ink); margin-top: 1px; }

  .address {
    position: absolute; left: 62px; top: 180px;
    font-size: 12.5px; line-height: 1.35; color: var(--ink);
  }
  .contacts {
    position: absolute; left: 62px; top: 222px;
    list-style: none; font-size: 12.5px; line-height: 1.35; color: var(--ink);
  }
  .contacts li { display: flex; align-items: center; gap: 7px; }
  .contacts svg { width: 10px; height: 10px; fill: var(--teal-deep); flex: none; }
</style>
</head>
<body>

  <section class="card card-front" aria-label="Business card front">
    <div class="deco-circle"></div>
    <div class="accent-bar"></div>
    <div class="wordmark"><span class="wordmark-dot"></span>little lanterns</div>

    <div class="person">
      <p class="person-name">Clara <span class="surname">Whitfield</span></p>
      <p class="person-role">Managing Director</p>
    </div>

    <p class="address">240 Alder Lane Riverton<br>OR 97321, United States</p>

    <ul class="contacts">
      <li>
        <svg viewBox="0 0 10 10" aria-hidden="true"><path d="M2 0.5 L3.6 2.8 L2.7 3.8 Q4 6.2 6.2 7.3 L7.2 6.4 L9.5 8 L8.4 9.6 Q3.5 9 0.4 1.6 Z"/></svg>
        (+1) 555.014.2200
      </li>
      <li>
        <svg viewBox="0 0 10 10" aria-hidden="true"><path d="M0 2 H10 V8.5 H0 Z M0.6 2.4 L5 5.6 L9.4 2.4" stroke="#eceef2" stroke-width="0.8"/></svg>
        info@littlelanterns.org
      </li>
      <li>
        <svg viewBox="0 0 10 10" aria-hidden="true"><circle cx="5" cy="5" r="4.6"/><path d="M0.6 5 H9.4 M5 0.5 Q2.4 5 5 9.5 M5 0.5 Q7.6 5 5 9.5" stroke="#eceef2" stroke-width="0.7" fill="none"/></svg>
        www.littlelanterns.org
      </li>
    </ul>
  </section>

  <section class="card card-back" aria-label="Business card back">
    <div class="deco-circle"></div>
    <div class="wordmark"><span class="wordmark-dot"></span>little lanterns</div>
  </section>

</body>
</html>
```